Business Card Design

New business card design

Target Market(s)

Residential & Commercial Property Managers

Industry/Entity Type

Plumbing Services

Contact Information for Business Card

Name - Rowan Keddle, title - Director, Phone Number - 0431 286 517, email - rowan@tbk-plumbing.com.au, Company ABN - 73 215 904 386,

Font styles to use
Sans Serif

Colors
0054AA
0677BA
7BADD7
CADEEF
E8F1F8

```html
<!DOCTYPE html>
<html lang="en">
<head>
<meta charset="utf-8">
<title>TBK Plumbing Services – Business Card</title>
<link rel="stylesheet" href="https://fonts.googleapis.com/css2?family=Source+Sans+3:ital,wght@0,300;0,400;0,600;1,600&display=swap">
<style>
  :root {
    --page: #fdfdfd;
    --card: #cae9f8;
    --accent: #2ca8e0;
    --ink: #1f252b;
    --muted: #6d6762;
    --white: #ffffff;
  }
  * { box-sizing: border-box; margin: 0; padding: 0; }
  html, body { width: 1000px; height: 1200px; overflow: hidden; background: var(--page); }
  body { position: relative; font-family: "Source Sans 3", sans-serif; color: var(--ink); }

  .card {
    position: absolute;
    left: 172px;
    width: 659px;
    height: 377px;
    background: var(--card);
    overflow: hidden;
  }
  .card--front { top: 170px; }
  .card--back { top: 659px; }

  .brand-name {
    position: absolute;
    left: 0; right: 0;
    text-align: center;
    font-weight: 600;
    color: var(--ink);
    letter-spacing: 0.02em;
    white-space: nowrap;
  }
  .card--front .brand-name { top: 128px; font-size: 50px; }
  .card--back .brand-name { top: 72px; font-size: 42px; }

  .abn-band { position: absolute; left: 0; bottom: 0; width: 659px; height: 48px; }
  .abn-text {
    position: absolute;
    left: 0; right: 0;
    bottom: 10px;
    text-align: center;
    font-weight: 300;
    font-size: 20px;
    color: var(--white);
  }

  .frame {
    position: absolute;
    left: 23px; top: 23px;
    width: 613px; height: 331px;
    border: 1.5px solid var(--muted);
  }

  .contact { position: absolute; left: 0; right: 0; text-align: center; }
  .contact__name { top: 206px; font-size: 28px; font-weight: 600; }
  .contact__title { top: 246px; font-size: 21px; font-weight: 600; font-style: italic; }
  .contact__line {
    font-size: 20px; font-weight: 300;
    display: flex; justify-content: center; align-items: center; gap: 8px;
  }
  .contact__phone { top: 279px; }
  .contact__email { top: 308px; }
  .icon { width: 16px; height: 16px; fill: var(--muted); flex: none; }
</style>
</head>
<body>

<section class="card card--front" aria-label="Business card front">
  <div class="brand-name">TBK Plumbing Services</div>
  <svg class="abn-band" viewBox="0 0 659 48" aria-hidden="true">
    <path fill="var(--accent)" d="M0 32 H171 Q186 32 196 20 Q207 0 228 0 H434 Q454 0 463 14 Q475 32 489 32 H659 V48 H0 Z"/>
  </svg>
  <div class="abn-text">ABN - 73 215 904 386</div>
</section>

<section class="card card--back" aria-label="Business card back">
  <div class="frame"></div>
  <div class="brand-name">TBK Plumbing Services</div>
  <div class="contact contact__name">Rowan Keddle</div>
  <div class="contact contact__title">Director</div>
  <div class="contact contact__line contact__phone">
    <svg class="icon" viewBox="0 0 16 16" aria-hidden="true">
      <path d="M3.6 1.2 5.7 3.4c.4.4.4 1 0 1.4L4.6 5.9c.9 2 2.5 3.6 4.5 4.5l1.1-1.1c.4-.4 1-.4 1.4 0l2.2 2.1c.4.4.4 1 0 1.4l-1.2 1.2c-.6.6-1.5.8-2.3.5C6.7 13.3 2.7 9.3 1.5 5.7c-.3-.8-.1-1.7.5-2.3l1.2-1.2c.1-.1.2-.1.4-.1z"/>
    </svg>
    <span>0431 286 517</span>
  </div>
  <div class="contact contact__line contact__email">
    <svg class="icon" viewBox="0 0 16 16" aria-hidden="true">
      <path d="M1 3.5h14v1.2L8 9 1 4.7z M1 6.3 8 10.6l7-4.3V13H1z"/>
    </svg>
    <span>rowan@tbk-plumbing.com.au</span>
  </div>
</section>

</body>
</html>
```